Business card design needed

I need a business card design for a new online retail business based in Australia. I am unsure of the exact content of what I will be selling but it will be probably women's clothing, accessories, gym wear, gifts and maybe homeware linen. I am wanting a classy design that portrays the image of class/style/upmarket.

Target Market(s)

predominantely women - 20-50 age group

Industry/Entity Type

Retail

Contact Information for Business Card

Quietly Golden
Renata Calloway
Director
ABN 73418250964
17 Harrow Crescent Linfield Park NSW 2391
ph: +61 427 905 184
sales@quietlygolden.com.au

Logo Text

I am open for suggestions here

Requirements
Must have
• The design must be both sides of the card

```html
<!DOCTYPE html>
<html lang="en">
<head>
<meta charset="utf-8">
<title>Quietly Golden – Business Card</title>
<link rel="stylesheet" href="https://fonts.googleapis.com/css2?family=Arimo:wght@400&display=swap">
<style>
  :root {
    --plum: #8a2b85;
    --plum-light: #a33c9b;
    --plum-deep: #7a2477;
    --amber: #f5921e;
    --card-white: #ffffff;
    --ink-grey: #5a5a5a;
    --backdrop: #ececec;
  }
  * { box-sizing: border-box; margin: 0; padding: 0; }
  html, body { width: 1200px; height: 900px; overflow: hidden; }
  body {
    background: var(--backdrop);
    font-family: "Arimo", Arial, sans-serif;
    display: flex;
    align-items: center;
    justify-content: center;
    gap: 40px;
  }
  .card {
    position: relative;
    width: 540px;
    height: 309px;
    background: var(--card-white);
    overflow: hidden;
    box-shadow: 0 2px 8px rgba(0,0,0,0.12);
  }
  .card-front .oval { position: absolute; inset: 0; }
  .card-front .brand {
    position: absolute;
    left: 0; right: 0; top: 50%;
    transform: translateY(-50%);
    display: flex;
    align-items: center;
    justify-content: center;
    gap: 14px;
    color: var(--card-white);
    font-size: 38px;
    letter-spacing: 0.5px;
  }
  .brand-dot {
    width: 18px; height: 18px;
    border-radius: 50%;
    background: var(--amber);
  }
  .card-back .brand-tile {
    position: absolute;
    left: 48px; top: 34px;
    width: 112px; height: 130px;
    background: linear-gradient(180deg, var(--amber) 0%, var(--plum-light) 100%);
    display: flex;
    align-items: flex-end;
    justify-content: center;
    padding-bottom: 16px;
  }
  .brand-tile .brand-name {
    color: var(--card-white);
    font-size: 15px;
    text-align: center;
    line-height: 1.2;
  }
  .details {
    position: absolute;
    left: 48px; top: 172px;
    color: var(--ink-grey);
    font-size: 12.5px;
    line-height: 1.35;
  }
  .details .person { color: var(--plum); font-size: 19px; line-height: 1.2; }
  .details .role { margin-bottom: 10px; }
  .details .address { margin-bottom: 10px; }
  .contact-line { display: flex; align-items: center; gap: 8px; }
  .contact-line svg { width: 12px; height: 12px; fill: var(--plum); flex: none; }
</style>
</head>
<body>
  <section class="card card-front">
    <svg class="oval" viewBox="0 0 540 309" width="540" height="309" aria-hidden="true">
      <defs>
        <linearGradient id="plum-fill" x1="0" y1="0" x2="1" y2="0">
          <stop offset="0" stop-color="#a33c9b"/>
          <stop offset="1" stop-color="#7a2477"/>
        </linearGradient>
      </defs>
      <ellipse cx="285" cy="150" rx="300" ry="225" transform="rotate(-22 285 150)" fill="#f5921e"/>
      <ellipse cx="272" cy="160" rx="292" ry="218" transform="rotate(-22 272 160)" fill="url(#plum-fill)"/>
    </svg>
    <div class="brand">
      <span class="brand-dot"></span>
      <span class="brand-name">Quietly Golden</span>
    </div>
  </section>

  <section class="card card-back">
    <div class="brand-tile">
      <span class="brand-name">Quietly Golden</span>
    </div>
    <div class="details">
      <p class="person">Renata Calloway</p>
      <p class="role">Director</p>
      <p class="address">ABN 73418250964 17 Harrow Crescent<br>Linfield Park NSW 2391</p>
      <p class="contact-line">
        <svg viewBox="0 0 24 24" aria-hidden="true"><path d="M6.6 10.8a15.1 15.1 0 0 0 6.6 6.6l2.2-2.2a1 1 0 0 1 1-.25 11.4 11.4 0 0 0 3.6.57 1 1 0 0 1 1 1V20a1 1 0 0 1-1 1A17 17 0 0 1 3 4a1 1 0 0 1 1-1h3.5a1 1 0 0 1 1 1c0 1.25.2 2.45.57 3.57a1 1 0 0 1-.25 1z"/></svg>
        +61 427 905 184
      </p>
      <p class="contact-line">
        <svg viewBox="0 0 24 24" aria-hidden="true"><path d="M2 5h20v14H2z M2 5l10 8 10-8" /></svg>
        sales@quietlygolden.com.au
      </p>
    </div>
  </section>
</body>
</html>
```